Homecare Design. I would like the color to be same as my business cards

Gentle Hearth & Caregiver Agency
I would something very light on the eyes.
Easy to read nothing complicated
I want something that demonstrate soft touch
Updates

My contact number has change cell: 203-555-0187 office: 2035550142

Target Market(s)

Elderly
people looking for someone to take care of there love ones
Target age starting at 50

Industry/Entity Type

Business

Font styles to use
Serif

Colors
3176b5
3276b5
85acd3
ceddec

Requirements
Must have

Nice to have
• I woluld like something like helping hands
Should not have
• I really don't care to see medical supplies, medication

```html
<!DOCTYPE html>
<html lang="en">
<head>
<meta charset="utf-8">
<title>Gentle Hearth &amp; Caregiver Agency – Postcard</title>
<link rel="stylesheet" href="https://fonts.googleapis.com/css2?family=Arimo:wght@400;700&family=Roboto:wght@300&family=Tinos:ital,wght@1,700&display=swap">
<style>
  :root {
    --backdrop: #181b1e;
    --paper: #ffffff;
    --brand: #3176b5;
    --brand-soft: #85acd3;
    --brand-mist: #ceddec;
    --brand-deep: #283b97;
    --ink-grey: #6d6d6d;
    --rule: #8a8a8a;
  }
  * { margin: 0; padding: 0; box-sizing: border-box; }
  html, body { width: 920px; height: 1200px; overflow: hidden; background: var(--backdrop); }
  body { position: relative; font-family: "Arimo", Arial, sans-serif; color: var(--brand); }

  .card { position: absolute; left: 90px; width: 724px; height: 561px; background: var(--paper); overflow: hidden; }
  .card--front { top: 24px; }
  .card--back { top: 611px; }

  /* Front */
  .front-backdrop {
    position: absolute; left: 0; top: 0; width: 724px; height: 470px;
    background: linear-gradient(to bottom, #eceef1 0%, #f3f4f6 55%, #ffffff 100%);
  }
  .hero-photo {
    position: absolute; left: 0; top: 0; width: 330px; height: 320px;
    background: radial-gradient(ellipse at 45% 45%, #d9a68a 0%, #e3c0ab 35%, #eeeeef 70%, rgba(243,244,246,0) 100%);
  }
  .headline { font-family: "Roboto", Arial, sans-serif; font-weight: 300; color: var(--brand); }
  .headline span { position: absolute; right: 38px; line-height: 1; white-space: nowrap; }
  .headline .caring { top: 69px; font-size: 62px; letter-spacing: 1px; }
  .headline .middle { top: 143px; font-size: 46px; }
  .headline .matter { top: 193px; font-size: 76px; letter-spacing: 1px; }
  .wave-band {
    position: absolute; left: 0; top: 326px; width: 724px; height: 30px;
    background: linear-gradient(to right, rgba(206,221,236,0.6) 0%, var(--brand-soft) 35%, var(--brand) 70%, var(--brand-deep) 100%);
    opacity: 0.9;
  }

  .agency-name { font-family: "Tinos", "Times New Roman", serif; font-style: italic; font-weight: 700; color: var(--brand); }
  .front-info { position: absolute; left: 0; right: 0; top: 385px; text-align: center; }
  .front-info .agency-name { font-size: 30px; line-height: 34px; }
  .front-info .cta { font-size: 18px; line-height: 22px; margin-top: 10px; }
  .front-info .phone { font-size: 30px; line-height: 34px; font-weight: 700; }
  .front-info .address { font-size: 16px; line-height: 20px; margin-top: 6px; }

  /* Back */
  .card--back .agency-name { position: absolute; left: 37px; top: 34px; font-size: 25px; }
  .intro { position: absolute; left: 38px; top: 84px; width: 290px; font-size: 13.4px; line-height: 17.3px; text-align: justify; }
  .services { position: absolute; left: 39px; top: 194px; font-size: 13.4px; line-height: 17.3px; }
  .services h2 { font-size: 15.5px; font-weight: 700; line-height: 18px; }
  .services ul { list-style: none; }
  .services li::before { content: "\2714"; margin-right: 3px; }
  .call-band { position: absolute; left: 0; top: 394px; width: 349px; height: 69px; background: var(--brand); color: #fff; padding: 11px 0 0 39px; font-size: 15px; line-height: 18px; }
  .call-band strong { font-weight: 700; }

  .mail-return { position: absolute; left: 355px; top: 85px; width: 190px; text-align: center; font-size: 13.4px; line-height: 16.5px; }
  .stamp-box { position: absolute; left: 580px; top: 43px; width: 95px; height: 108px; border: 1px solid #a9a9a9; padding: 26px 0 0 24px; color: var(--ink-grey); font-size: 17px; line-height: 21px; }
  .address-line { position: absolute; left: 385px; width: 296px; height: 1px; background: var(--rule); }
</style>
</head>
<body>

<section class="card card--front">
  <div class="front-backdrop"></div>
  <div class="hero-photo" role="img" aria-label="Photograph of a caregiver's hands gently holding an elderly person's hand on white linen"></div>
  <h1 class="headline">
    <span class="caring">CARING</span>
    <span class="middle">FOR THOSE THAT</span>
    <span class="matter">MATTER</span>
  </h1>
  <div class="wave-band" role="img" aria-label="Decorative flowing blue wave across the card"></div>
  <div class="front-info">
    <p class="agency-name">Gentle Hearth &amp; Caregiver Agency</p>
    <p class="cta">To schedule an appointment, please call:</p>
    <p class="phone">(203-555-0142)</p>
    <p class="address">Gentle Hearth and Caregiver Agency<br>48 LINDEN AVE WESTBROOK CT 06498 US</p>
  </div>
</section>

<section class="card card--back">
  <p class="agency-name">Gentle Hearth &amp; Caregiver Agency</p>
  <p class="intro">Gentle Hearth &amp; Caregiver Agency, assist elderly clients who need assistance in or out of the home. Our home care services to our clients to assist them to lead dignified and independent lives in the comfort and safety of there own homes</p>
  <div class="services">
    <h2>Our Services</h2>
    <ul>
      <li>Assistance with Daily Living</li>
      <li>Light cooking</li>
      <li>Light Housekeeping</li>
      <li>Running errands</li>
      <li>Accompaniment to Doctors visits</li>
      <li>Laundry</li>
      <li>In and out home activities</li>
      <li>Medication reminders</li>
      <li>Hours of services range from 4 hrs to</li>
      <li>Live-in services</li>
    </ul>
  </div>
  <div class="call-band">
    To schedule an appointment, please call:<br>
    Office - <strong>203-555-0142)</strong><br>
    <strong>Cell - 203-555-0187</strong>
  </div>
  <p class="mail-return">Gentle Hearth<br>and Caregiver Agency<br>48 LINDEN AVE WESTBROOK<br>CT 06498 US</p>
  <div class="stamp-box">Place<br>Stamp<br>Here</div>
  <div class="address-line" style="top:267px"></div>
  <div class="address-line" style="top:327px"></div>
  <div class="address-line" style="top:388px"></div>
</section>

</body>
</html>
```